Rapid Pulse Tiny Track Karts

We are looking for a full web site for our race car category that allows us to edit and update some of the content. We would like the site to feel modern and attractive with the following features: 1. Event calender (with the ability for us to update) 2. Social media/ clip wave links 3. photo gallery (with the ability for us to update) 4. Member area with log in access (controlled access) - this area to include access to category regulations for up to 5 types of cars separately 5. Championship ladder for up to 5 different groups 6. sponsor page and sponsors scrolling across bottom of all pages. Please find attached our logo to be used and for reference on color/ style 7. page to show merchandise but no need for a store.

Industry/Entity Type

Motor racing category

Coding

Coded - Design and coding required

Number of Pages Required

5+ page

Colors
0054AA
0677BA
7BADD7
CADEEF
E8F1F8
FFF300
FFF600
FEFA6F
FFFEC7
FFFEE8
EB3D1F
EC4F4E
F09395
F8D3D4
FCEDEE

Requirements
Must have
• Ability to update calender/photo gallery/championship ladder including points/ notice board - Members section

```html
<!DOCTYPE html>
<html lang="en">
<head>
<meta charset="utf-8">
<title>Rapid Pulse Tiny Track Karts</title>
<link rel="stylesheet" href="https://fonts.googleapis.com/css2?family=Bruno+Ace&family=Montserrat:wght@400;500;600;700&display=swap">
<style>
:root{
  --black:#000;
  --yellow:#fbd52a;
  --yellow-deep:#f2c81c;
  --blue:#0a5bd8;
  --navy:#232f91;
  --ink:#111;
  --grey:#555;
  --footer:#333;
  --white:#fff;
  --red:#eb3d1f;
}
*{box-sizing:border-box;margin:0;padding:0}
html,body{width:1200px;height:3451px;overflow:hidden;background:var(--white);font-family:"Montserrat",sans-serif;color:var(--ink)}
.page{position:relative;width:1200px;height:3451px}
.abs{position:absolute}
.heading{font-family:"Bruno Ace",sans-serif;font-weight:400}
/* top bar */
.topbar{left:0;top:0;width:1200px;height:79px;background:var(--black)}
.brand{left:138px;top:8px;width:164px;height:60px;border:2px solid var(--white);border-radius:6px;display:flex;align-items:center;justify-content:center;text-align:center;color:var(--white);font-family:"Montserrat",sans-serif;font-weight:700;font-size:12px;line-height:1.2;padding:4px}
.phone{right:112px;top:22px;display:flex;align-items:center;gap:14px;color:var(--white);font-weight:700;font-size:24px}
.phone-ico{width:34px;height:34px;border-radius:50%;background:var(--yellow);display:flex;align-items:center;justify-content:center}
/* nav */
.nav{left:0;top:79px;width:1200px;height:51px;background:var(--yellow)}
.nav ul{position:absolute;left:111px;top:0;height:51px;display:flex;align-items:center;list-style:none;font-family:"Bruno Ace",sans-serif;font-size:16px}
.nav li+li::before{content:"|";margin:0 24px;font-family:"Montserrat",sans-serif}
.login-panel{position:absolute;left:0;top:0}
.login{right:122px;top:92px;display:flex;align-items:center;gap:10px;font-family:"Bruno Ace",sans-serif;font-size:17px}
/* hero */
.hero{left:0;top:130px;width:1200px;height:607px}
.hero-text{left:111px;top:258px;color:var(--white)}
.hero-kicker{font-family:"Bruno Ace",sans-serif;font-size:19px;letter-spacing:.5px}
.hero-title{font-size:33px;line-height:40px;margin-top:8px}
.hero-copy{font-size:15.5px;line-height:26px;width:420px;margin-top:18px}
/* events */
.section-title{width:1200px;text-align:center;font-size:35px;left:0}
.datebox{left:111px;top:899px;width:218px;height:37px;border:1px solid #444;display:flex;align-items:center;justify-content:space-between;padding:0 14px 0 55px;font-size:16px}
.event{width:459px;height:97px;display:flex;background:var(--white);box-shadow:0 2px 6px rgba(0,0,0,.18)}
.event-date{width:161px;color:var(--white);display:flex;flex-direction:column;justify-content:center;align-items:center;font-family:"Bruno Ace",sans-serif;font-size:25px;line-height:33px}
.event-date.blue{background:var(--blue)}
.event-date.navy{background:var(--navy)}
.event-body{flex:1;padding:10px 14px 0 9px;font-size:15.5px;line-height:21px;color:var(--grey);position:relative}
.event-body strong{color:var(--ink);font-weight:600;display:block}
.book{position:absolute;right:14px;bottom:5px;color:var(--blue);font-weight:600;font-size:14px}
/* championship */
.champ{left:0;top:1388px;width:1200px;height:458px;background:linear-gradient(100deg,#f6d23a 0%,#f2cc33 45%,#eec72f 70%,#f7d645 100%)}
.champ-copy{left:111px;top:1537px;width:495px;font-size:15.5px;line-height:26px;color:#333}
.dots{left:533px;top:1755px;display:flex;gap:5px}
.dots span{width:30px;height:4px;background:var(--ink)}
.dots span.on{background:var(--navy)}
/* gallery */
.g-title{left:498px;top:1922px;font-size:35px}
.g-copy{left:501px;top:1987px;width:587px;font-size:15.5px;line-height:26px;color:#333;text-align:justify}
.sq-btn{width:30px;height:30px;background:var(--black);display:flex;align-items:center;justify-content:center}
.thumb{top:2159px;width:131px;height:145px}
/* merch */
.merch{left:0;top:2391px;width:1200px;height:510px;background:radial-gradient(ellipse at 50% 40%,#fde15a 0%,#f6d12f 55%,#f0c521 100%)}
.card{width:252px;background:var(--white);text-align:center}
.card-img{height:174px}
.card-name{font-family:"Bruno Ace",sans-serif;font-size:19px;padding-top:8px}
.circ-btn{width:40px;height:40px;border-radius:50%;background:var(--black);display:flex;align-items:center;justify-content:center}
/* sponsors */
.sponsor{top:3068px;width:150px;height:52px;display:flex;align-items:center;justify-content:center;gap:8px;font-weight:700;font-size:21px;color:#333}
.dot{width:14px;height:14px;border-radius:50%}
/* footer */
.footer{left:0;top:3204px;width:1200px;height:247px;background:var(--footer)}
.f-brand{left:518px;top:3226px;width:164px;height:60px;border:2px solid var(--white);border-radius:6px;display:flex;align-items:center;justify-content:center;text-align:center;color:var(--white);font-weight:700;font-size:12px;line-height:1.2;padding:4px}
.f-nav{left:0;top:3302px;width:1200px;display:flex;justify-content:center;list-style:none;color:var(--white);font-family:"Bruno Ace",sans-serif;font-size:16px}
.f-nav li+li::before{content:"|";margin:0 24px;font-family:"Montserrat",sans-serif}
.social{left:538px;top:3344px;display:flex;gap:21px}
.social span{width:26px;height:26px;border-radius:50%;background:var(--white)}
.copy{left:0;top:3414px;width:1200px;text-align:center;color:var(--white);font-size:15px}
</style>
</head>
<body>
<div class="page">

  <header>
    <div class="abs topbar"></div>
    <div class="abs brand">Rapid Pulse<br>Tiny Track Karts</div>
    <div class="abs phone">
      <span class="phone-ico"><svg width="18" height="18" viewBox="0 0 24 24"><path fill="#000" d="M6.6 10.8a15.1 15.1 0 0 0 6.6 6.6l2.2-2.2c.3-.3.7-.4 1-.2 1.1.4 2.3.6 3.6.6.6 0 1 .4 1 1V20c0 .6-.4 1-1 1A17 17 0 0 1 3 4c0-.6.4-1 1-1h3.5c.6 0 1 .4 1 1 0 1.3.2 2.5.6 3.6.1.3 0 .7-.2 1z"/></svg></span>
      +1 555 010 0199
    </div>
    <nav class="abs nav">
      <svg class="login-panel" width="1200" height="51"><polygon points="958,0 1200,0 1200,51 890,51" fill="#fff"/></svg>
      <ul><li>Home</li><li>Event</li><li>Gallery</li><li>Championship</li><li>Sponsor</li><li>Merchandise</li></ul>
    </nav>
    <div class="abs login">Login In
      <svg width="26" height="26" viewBox="0 0 24 24" fill="none" stroke="#000" stroke-width="2"><path d="M14 3h6v18h-6M3 12h12M11 8l4 4-4 4"/></svg>
    </div>
  </header>

  <section class="abs hero">
    <svg width="1200" height="607" viewBox="0 0 1200 607">
      <defs>
        <linearGradient id="heroShade" x1="0" y1="0" x2="1" y2="1">
          <stop offset="0" stop-color="#2b2b2b"/><stop offset=".55" stop-color="#4a4a4a"/><stop offset="1" stop-color="#1c1c1c"/>
        </linearGradient>
      </defs>
      <polygon points="0,436 810,607 1200,428 1200,442 810,600 0,452" fill="#fbd52a"/>
      <polygon points="0,0 1200,0 1200,428 810,596 0,436" fill="url(#heroShade)" role="img" aria-label="Black and red race car on a pit lane"/>
    </svg>
  </section>
  <div class="abs hero-text">
    <div class="hero-kicker">WELCOME TO</div>
    <h1 class="heading hero-title">RAPID PULSE TINY<br>TRACK KARTS</h1>
    <p class="hero-copy">Lorem ipsum dolor sit amet, consectetur adipiscing elit, sed do eiusmod tempor incididunt ut labore et dolore magna aliqua.</p>
  </div>

  <section>
    <h2 class="abs heading section-title" style="top:815px">Event Calendar</h2>
    <div class="abs datebox">Oct 2023
      <svg width="20" height="20" viewBox="0 0 24 24"><path fill="#222" d="M5 4h2V2h2v2h6V2h2v2h2a1 1 0 0 1 1 1v16a1 1 0 0 1-1 1H5a1 1 0 0 1-1-1V5a1 1 0 0 1 1-1zm1 6v10h12V10zm2 2h2v2H8zm4 0h2v2h-2zm4 0h2v2h-2zm-8 4h2v2H8zm4 0h2v2h-2zm4 0h2v2h-2z"/></svg>
    </div>

    <div class="abs event" style="left:112px;top:974px"><div class="event-date blue">02<span>OCT</span></div><div class="event-body"><strong>Lorem ipsum dolor sit amet,</strong>Lorem ipsum dolor sit amet,<br>consectetur adipiscing<span class="book">Book Now →</span></div></div>
    <div class="abs event" style="left:631px;top:974px"><div class="event-date navy">18<span>OCT</span></div><div class="event-body"><strong>Lorem ipsum dolor sit amet,</strong>Lorem ipsum dolor sit amet,<br>consectetur adipiscing<span class="book">Book Now →</span></div></div>
    <div class="abs event" style="left:112px;top:1089px"><div class="event-date navy">09<span>OCT</span></div><div class="event-body"><strong>Lorem ipsum dolor sit amet,</strong>Lorem ipsum dolor sit amet,<br>consectetur adipiscing<span class="book">Book Now →</span></div></div>
    <div class="abs event" style="left:631px;top:1089px"><div class="event-date blue">24<span>OCT</span></div><div class="event-body"><strong>Lorem ipsum dolor sit amet,</strong>Lorem ipsum dolor sit amet,<br>consectetur adipiscing<span class="book">Book Now →</span></div></div>
    <div class="abs event" style="left:112px;top:1205px"><div class="event-date blue">12<span>OCT</span></div><div class="event-body"><strong>Lorem ipsum dolor sit amet,</strong>Lorem ipsum dolor sit amet,<br>consectetur adipiscing<span class="book">Book Now →</span></div></div>
    <div class="abs event" style="left:631px;top:1205px"><div class="event-date navy">27<span>OCT</span></div><div class="event-body"><strong>Lorem ipsum dolor sit amet,</strong>Lorem ipsum dolor sit amet,<br>consectetur adipiscing<span class="book">Book Now →</span></div></div>
  </section>

  <section>
    <div class="abs champ" role="img" aria-label="Blurred yellow race car background"></div>
    <h2 class="abs heading section-title" style="top:1467px">Championship</h2>
    <p class="abs champ-copy">Lorem ipsum dolor sit amet, consectetur adipiscing elit, sed do eiusmod tempor incididunt ut labore et dolore magna aliqua. Quis ipsum suspendisse ultrices gravida. Risus commodo viverra maecenas accumsan lacus vel facilisis.</p>
    <div class="abs" style="left:623px;top:1536px;width:110px;height:200px;background:linear-gradient(#e6b53a,#a8741a);border-radius:40px 40px 8px 8px" role="img" aria-label="Gold trophy with stars"></div>
    <svg class="abs" style="left:700px;top:1538px" width="360" height="185" viewBox="0 0 360 185">
      <defs><linearGradient id="champPhoto" x1="0" y1="0" x2="1" y2="1"><stop offset="0" stop-color="#6fa6d8"/><stop offset=".5" stop-color="#c9a27e"/><stop offset="1" stop-color="#2b3f7a"/></linearGradient></defs>
      <polygon points="60,3 290,3 355,92 290,182 60,182 3,92" fill="url(#champPhoto)" stroke="#111" stroke-width="5" role="img" aria-label="Celebrating race drivers"/>
    </svg>
    <div class="abs dots"><span></span><span></span><span></span><span class="on"></span></div>
  </section>

  <section>
    <div class="abs" style="left:111px;top:1938px;width:356px;height:356px;border-radius:50%;background:radial-gradient(circle at 50% 55%,#2c4a8a 0%,#3a5596 30%,#c07a3e 60%,#d99a5a 100%)" role="img" aria-label="Rally car racing through desert sand"></div>
    <h2 class="abs heading g-title">Gallery</h2>
    <p class="abs g-copy">Lorem ipsum dolor sit amet, consectetur adipiscing elit, sed do eiusmod tempor incididunt ut labore et dolore magna aliqua. Quis ipsum suspendisse ultrices gravida. Risus commodo viverra maecenas accumsan lacus vel facilisis.</p>
    <div class="abs sq-btn" style="left:1011px;top:2111px"><svg width="14" height="14" viewBox="0 0 24 24"><path d="M15 4 7 12l8 8" stroke="#fff" stroke-width="3" fill="none"/></svg></div>
    <div class="abs sq-btn" style="left:1058px;top:2111px"><svg width="14" height="14" viewBox="0 0 24 24"><path d="M9 4l8 8-8 8" stroke="#fff" stroke-width="3" fill="none"/></svg></div>
    <div class="abs thumb" style="left:501px;background:linear-gradient(#f0f0f0,#c23030 60%,#666)" role="img" aria-label="Red race car"></div>
    <div class="abs thumb" style="left:641px;background:linear-gradient(#8a8f99,#b02020 55%,#d8d8d8)" role="img" aria-label="Formula race car"></div>
    <div class="abs thumb" style="left:781px;background:linear-gradient(#9bb7cf,#e8eef5 55%,#5a6470)" role="img" aria-label="White and blue touring car"></div>
    <div class="abs thumb" style="left:920px;background:linear-gradient(135deg,#333,#111 50%,#8a1a1a)" role="img" aria-label="Car drifting past chequered line"></div>
  </section>

  <section>
    <div class="abs merch" role="img" aria-label="Yellow motion blur background"></div>
    <h2 class="abs heading section-title" style="top:2470px">Merchandise</h2>
    <div class="abs circ-btn" style="left:111px;top:2659px"><svg width="16" height="16" viewBox="0 0 24 24"><path d="M15 4 7 12l8 8" stroke="#fff" stroke-width="3" fill="none"/></svg></div>
    <div class="abs circ-btn" style="left:1048px;top:2659px"><svg width="16" height="16" viewBox="0 0 24 24"><path d="M9 4l8 8-8 8" stroke="#fff" stroke-width="3" fill="none"/></svg></div>
    <div class="abs card" style="left:173px;top:2541px;height:216px"><div class="card-img" style="background:linear-gradient(#3a3a3a,#1f8a78 55%,#2a2a2a)" role="img" aria-label="Green race car drifting with smoke"></div><div class="card-name">Product 1</div></div>
    <div class="abs card" style="left:475px;top:2541px;height:273px"><div class="card-img" style="background:linear-gradient(135deg,#1a1a1a,#4a4a4a 60%,#c8a08a)" role="img" aria-label="Hand touching a racing tyre"></div><div class="card-name" style="padding-top:14px">Product 2</div><div style="font-size:15px;color:#555;margin-top:2px">Lorem ipsum dolor sit</div><div style="font-size:14px;font-weight:600;color:var(--blue);margin-top:10px">View More →</div></div>
    <div class="abs card" style="left:778px;top:2541px;height:216px"><div class="card-img" style="background:radial-gradient(circle at 50% 50%,#f29b2a,#e84a2a 45%,#f4f4f4 75%)" role="img" aria-label="Orange racing helmet"></div><div class="card-name">Product 3</div></div>
  </section>

  <section>
    <h2 class="abs heading section-title" style="top:2957px">Sponsors</h2>
    <svg class="abs" style="left:108px;top:3078px" width="24" height="36" viewBox="0 0 24 36"><path d="M18 4 6 18l12 14" stroke="#111" stroke-width="4" fill="none"/></svg>
    <svg class="abs" style="left:1068px;top:3078px" width="24" height="36" viewBox="0 0 24 36"><path d="M6 4l12 14-12 14" stroke="#111" stroke-width="4" fill="none"/></svg>
    <div class="abs sponsor" style="left:202px">Brightloom<span class="dot" style="background:#3bc24a"></span></div>
    <div class="abs sponsor" style="left:418px"><span class="dot" style="background:#c8202a"></span>Norvale</div>
    <div class="abs sponsor" style="left:632px">Kestrel Co<span class="dot" style="background:var(--red)"></span></div>
    <div class="abs sponsor" style="left:848px"><span class="dot" style="background:#a0683a"></span>Ridgeway</div>
  </section>

  <footer>
    <div class="abs footer"></div>
    <div class="abs f-brand">Rapid Pulse<br>Tiny Track Karts</div>
    <ul class="abs f-nav"><li>Home</li><li>Event</li><li>Gallery</li><li>Championship</li><li>Sponsor</li><li>Merchandise</li></ul>
    <div class="abs social" aria-label="Social links: community, video, clip wave"><span></span><span></span><span></span></div>
    <p class="abs copy">© 2023 Rapid Pulse Tiny Track Karts.All Rights Reserved.</p>
  </footer>

</div>
</body>
</html>
```